Business card for medical clinic

I need an upmarket, modern medical/health business card for my clinic

Contact Information for Business Card

name, address, email, qr code

```html
<!DOCTYPE html>
<html lang="en">
<head>
<meta charset="utf-8">
<title>Aldren Care Partners – Business Card</title>
<link href="https://fonts.googleapis.com/css2?family=Montserrat:wght@400;500;700&display=swap" rel="stylesheet">
<style>
  :root {
    --backdrop: #8a7358;
    --card-navy: #1e2a45;
    --card-shadow: rgba(0, 0, 0, 0.55);
    --accent-blue: #2ba6e0;
    --brand-teal: #2a6f9a;
    --text-white: #ffffff;
    --text-soft: #e8ecf3;
    --mark-blue: #3a55b8;
    --mark-navy: #17213a;
  }
  * { margin: 0; padding: 0; box-sizing: border-box; }
  html, body {
    width: 900px;
    height: 1200px;
    overflow: hidden;
  }
  body {
    position: relative;
    background: var(--backdrop);
    font-family: "Montserrat", sans-serif;
  }
  .card {
    position: absolute;
    background: var(--card-navy);
    border-radius: 24px;
    box-shadow: 0 8px 18px var(--card-shadow);
    overflow: hidden;
  }
  .card-front { left: 80px; top: 130px; width: 742px; height: 442px; }
  .card-back  { left: 78px; top: 637px; width: 744px; height: 441px; }

  /* Front */
  .brand-name {
    position: absolute;
    left: 34px;
    top: 48px;
    font-size: 24px;
    font-weight: 500;
    letter-spacing: 1.5px;
    color: var(--brand-teal);
    text-transform: uppercase;
  }
  .person {
    position: absolute;
    right: 51px;
    top: 40px;
    text-align: right;
  }
  .person-name {
    font-size: 25px;
    font-weight: 700;
    color: var(--accent-blue);
    line-height: 1.2;
  }
  .person-title {
    font-size: 15px;
    font-weight: 500;
    color: var(--text-white);
    margin-top: 2px;
  }
  .address {
    position: absolute;
    left: 41px;
    top: 250px;
    font-size: 16px;
    line-height: 20px;
    color: var(--text-soft);
  }
  .contact-list {
    position: absolute;
    left: 41px;
    top: 328px;
    list-style: none;
  }
  .contact-item {
    display: flex;
    align-items: center;
    gap: 11px;
    height: 31.5px;
    font-size: 16px;
    color: var(--text-soft);
  }
  .contact-icon { width: 15px; height: 15px; fill: var(--accent-blue); }
  .front-decoration {
    position: absolute;
    left: 440px;
    top: 180px;
    width: 260px;
    height: 245px;
    border-radius: 50%;
    background: radial-gradient(circle at 40% 40%, rgba(58, 85, 184, 0.35), rgba(30, 42, 69, 0) 70%);
  }

  /* Back */
  .back-pattern {
    position: absolute;
    inset: 0;
    background: linear-gradient(150deg, rgba(58, 85, 184, 0.55) 0%, rgba(58, 85, 184, 0.18) 35%, rgba(23, 33, 58, 0.35) 60%, rgba(23, 33, 58, 0.5) 100%);
  }
  .back-brand {
    position: absolute;
    left: 355px;
    top: 273px;
    display: flex;
    align-items: center;
    gap: 10px;
  }
  .back-brand-dot {
    width: 40px;
    height: 40px;
    border-radius: 50%;
    background: var(--text-white);
  }
  .back-brand-name {
    font-size: 17px;
    font-weight: 500;
    letter-spacing: 1px;
    color: var(--text-white);
    text-transform: uppercase;
  }
</style>
</head>
<body>

  <section class="card card-front">
    <div class="brand-name">Aldren Care Partners</div>

    <div class="person">
      <div class="person-name">Daniel Hart</div>
      <div class="person-title">Managing Director</div>
    </div>

    <div class="address">
      248 Cedar Ridge Road<br>
      Fairview, TN 37062
    </div>

    <ul class="contact-list">
      <li class="contact-item">
        <svg class="contact-icon" viewBox="0 0 24 24" aria-hidden="true"><path d="M6.6 10.8a15.1 15.1 0 0 0 6.6 6.6l2.2-2.2a1 1 0 0 1 1-.25 11.4 11.4 0 0 0 3.6.57 1 1 0 0 1 1 1V20a1 1 0 0 1-1 1A17 17 0 0 1 3 4a1 1 0 0 1 1-1h3.5a1 1 0 0 1 1 1c0 1.25.2 2.45.57 3.6a1 1 0 0 1-.25 1z"/></svg>
        555.204.7730
      </li>
      <li class="contact-item">
        <svg class="contact-icon" viewBox="0 0 24 24" aria-hidden="true"><path d="M2 5h20v2l-10 6L2 7zM2 9l10 6 10-6v10H2z"/></svg>
        hello@aldrencare.com
      </li>
      <li class="contact-item">
        <svg class="contact-icon" viewBox="0 0 24 24" aria-hidden="true"><path d="M12 2a10 10 0 1 0 0 20 10 10 0 0 0 0-20zm6.9 6h-3a15.6 15.6 0 0 0-1.4-3.6A8 8 0 0 1 18.9 8zM12 4a14 14 0 0 1 1.9 4h-3.8A14 14 0 0 1 12 4zM4.3 14a8 8 0 0 1 0-4h3.4a16.5 16.5 0 0 0 0 4zm.8 2h3a15.6 15.6 0 0 0 1.4 3.6A8 8 0 0 1 5.1 16zm3-8h-3a8 8 0 0 1 4.4-3.6A15.6 15.6 0 0 0 8.1 8zM12 20a14 14 0 0 1-1.9-4h3.8A14 14 0 0 1 12 20zm2.3-6H9.7a14.7 14.7 0 0 1 0-4h4.6a14.7 14.7 0 0 1 0 4zm.2 5.6a15.6 15.6 0 0 0 1.4-3.6h3a8 8 0 0 1-4.4 3.6zm1.8-5.6a16.5 16.5 0 0 0 0-4h3.4a8 8 0 0 1 0 4z"/></svg>
        www.aldrencare.com
      </li>
    </ul>

    <div class="front-decoration" role="img" aria-label="Large embossed brand emblem decoration"></div>
  </section>

  <section class="card card-back">
    <div class="back-pattern" role="img" aria-label="Repeating brand emblem pattern fading from blue to navy"></div>
    <div class="back-brand">
      <span class="back-brand-dot"></span>
      <span class="back-brand-name">Aldren Care Partners</span>
    </div>
  </section>

</body>
</html>
```